Automotive component supplier needs a business card design

We need a business card design for our company called Velran Global Components Ltd based in the UK. We are a supplier of interior and exterior components to premium car manufacturers such as Corvel Ashby, Hadley Fenn, Marquist and Tavarelli. We would like to see a modern business card design that uses the colour blue.

Target Market(s)

Premium automotive car manufacturers.

Industry/Entity Type

Automotive

Contact Information for Business Card

Company Name : Velran Global Components Limited
Address: 17 Marlow Yard, Upper Heath, Warwick, CV31 8QL, United Kingdom
Web Address : www.velrancomponents-example.co.uk

Font styles to use
Other font styles liked:
• Helvetica

Colors
3176b5
0255a3
85acd3
cfdeed
cee9f5
85cae6
34a6d7
0692cd
9bcb3c

Requirements
Must have
• Clear company logo and a mixture of blue colours.
Nice to have
• A high quality modern image.
Should not have
• Multiple colours.

```html
<!DOCTYPE html>
<html lang="en">
<head>
<meta charset="utf-8">
<title>Velran Global Components – Business Card</title>
<link href="https://fonts.googleapis.com/css2?family=Arimo:wght@400;700&display=swap" rel="stylesheet">
<style>
  :root {
    --bg: #2b2b2d;
    --blue: #0692cd;
    --blue-deep: #0f86c9;
    --blue-light: #34a6d7;
    --blue-pattern: #2a9fd4;
    --green: #9bcb3c;
    --white: #ffffff;
  }
  * { margin: 0; padding: 0; box-sizing: border-box; }
  html, body { width: 1200px; height: 900px; overflow: hidden; }
  body {
    background: var(--bg);
    font-family: "Arimo", Helvetica, Arial, sans-serif;
    position: relative;
  }
  .card {
    position: absolute;
    left: 285px;
    width: 630px;
    height: 360px;
    overflow: hidden;
    box-shadow: 0 10px 30px rgba(0,0,0,0.45);
  }
  .card-back { top: 50px; background: var(--blue-light); }
  .card-front { top: 490px; background: var(--white); }

  /* back */
  .back-texture {
    position: absolute; inset: 0;
    background: linear-gradient(135deg, var(--blue-pattern), var(--blue-light));
  }
  .back-logo {
    position: absolute; right: 60px; bottom: 110px;
    color: var(--white); text-align: left;
  }
  .wordmark {
    font-weight: 700; font-size: 52px; letter-spacing: 2px; line-height: 1;
    display: flex; align-items: center; gap: 10px;
  }
  .wordmark .dot {
    width: 12px; height: 12px; background: var(--green); display: inline-block;
  }
  .tagline {
    font-weight: 700; font-size: 13px; letter-spacing: 2.4px; margin-top: 6px;
    text-transform: uppercase;
  }

  /* front */
  .front-art { position: absolute; inset: 0; }
  .front-logo { position: absolute; left: 34px; top: 84px; color: var(--blue); }
  .front-logo .tagline { color: var(--blue); }
  .address {
    position: absolute; left: 34px; top: 226px;
    color: var(--blue); font-size: 15px; line-height: 1.35;
  }
  .contact {
    position: absolute; right: 24px; top: 100px;
    text-align: right; color: var(--white);
  }
  .contact .name {
    font-size: 17px; letter-spacing: 2.5px; text-transform: uppercase; font-weight: 400;
    line-height: 1.2;
  }
  .contact .role { color: var(--green); font-size: 13px; margin-bottom: 8px; }
  .contact ul { list-style: none; }
  .contact li {
    font-size: 12.5px; line-height: 1.5;
    display: flex; justify-content: flex-end; align-items: center; gap: 7px;
  }
  .contact li svg { width: 10px; height: 10px; flex: none; }
</style>
</head>
<body>

<section class="card card-back">
  <div class="back-texture" role="img" aria-label="Repeating brand pattern in tonal blues"></div>
  <div class="back-logo">
    <div class="wordmark"><span class="dot"></span>VELRAN</div>
    <div class="tagline">Global Components</div>
  </div>
</section>

<section class="card card-front">
  <svg class="front-art" viewBox="0 0 630 360" width="630" height="360" aria-hidden="true">
    <path d="M360 172 C330 262 278 306 160 313 C100 316 40 311 0 306" fill="none" stroke="var(--blue-deep)" stroke-width="2"/>
    <path d="M630 16 C430 20 370 80 350 190 C320 270 270 318 160 324 C100 327 40 322 0 316 L0 360 L630 360 Z" fill="var(--green)"/>
    <path transform="translate(6,8)" d="M630 16 C430 20 370 80 350 190 C320 270 270 318 160 324 C100 327 40 322 0 316 L0 360 L630 360 Z" fill="var(--white)"/>
    <path transform="translate(10,13)" d="M630 16 C430 20 370 80 350 190 C320 270 270 318 160 324 C100 327 40 322 0 316 L0 360 L630 360 Z" fill="var(--blue-deep)"/>
    <path d="M0 316 L0 360 L10 360 L10 329 Z" fill="var(--blue-deep)"/>
    <rect x="0" y="348" width="630" height="12" fill="var(--green)"/>
  </svg>

  <div class="front-logo">
    <div class="wordmark"><span class="dot"></span>VELRAN</div>
    <div class="tagline">Global Components</div>
  </div>

  <p class="address">17 Marlow Yard, Upper Heath<br>Warwick, CV31 8QL, UK</p>

  <div class="contact">
    <p class="name">Liam Harcourt</p>
    <p class="role">Director</p>
    <ul>
      <li>780 555-0142
        <svg viewBox="0 0 10 10"><path d="M2 1 L4 1 L4.5 3 L3.5 4 C4 5.5 5 6.5 6 6.5 L7 5.5 L9 6 L9 8 C5 9 1 5 2 1 Z" fill="var(--green)"/></svg></li>
      <li>780 555-0187
        <svg viewBox="0 0 10 10"><rect x="2.5" y="0.5" width="5" height="9" rx="1" fill="none" stroke="var(--green)"/></svg></li>
      <li>velrancomponents@example.com
        <svg viewBox="0 0 10 10"><rect x="0.5" y="2" width="9" height="6" fill="var(--green)"/><path d="M0.5 2 L5 5.5 L9.5 2" fill="none" stroke="var(--blue-deep)" stroke-width="0.8"/></svg></li>
      <li>www.velrancomponents-example.co.uk
        <svg viewBox="0 0 10 10"><circle cx="5" cy="5" r="4.5" fill="var(--green)"/><path d="M0.5 5 H9.5 M5 0.5 C2.5 3 2.5 7 5 9.5 M5 0.5 C7.5 3 7.5 7 5 9.5" fill="none" stroke="var(--blue-deep)" stroke-width="0.7"/></svg></li>
    </ul>
  </div>
</section>

</body>
</html>
```